I need a business card design for a new business based in South West Australia.
I specialize in residential window cleaning & general handyman maintenance.

Dale Marsh - 412 SILVER HAWK DETAILING
- Window Cleaning
- House Maintenance

```html
<!DOCTYPE html>
<html lang="en">
<head>
<meta charset="utf-8">
<title>412 Silver Hawk Detailing – Business Card</title>
<link href="https://fonts.googleapis.com/css2?family=Old+Standard+TT:wght@400;700&display=swap" rel="stylesheet">
<style>
  :root {
    --page-bg: #e9e6e1;
    --ink: #111111;
    --photo-sky: #b7cde8;
    --photo-mid: #cfdcea;
    --photo-grass: #6fae4a;
  }
  * { margin: 0; padding: 0; box-sizing: border-box; }
  html, body {
    width: 1200px;
    height: 892px;
    overflow: hidden;
    background: var(--page-bg);
  }
  .card {
    position: absolute;
    left: 90px;
    top: 156px;
    width: 1020px;
    height: 580px;
    border-radius: 34px;
    overflow: hidden;
    box-shadow: 0 10px 30px rgba(0,0,0,0.18);
    font-family: "Old Standard TT", "Times New Roman", serif;
    color: var(--ink);
  }
  .card__photo {
    position: absolute;
    inset: 0;
    background: linear-gradient(180deg, var(--photo-sky) 0%, var(--photo-mid) 55%, var(--photo-grass) 100%);
  }
  .brand {
    position: absolute;
    left: 60px;
    top: 66px;
  }
  .brand__name {
    font-size: 42px;
    font-weight: 700;
    letter-spacing: 0.5px;
    white-space: nowrap;
  }
  .brand__tagline {
    margin-top: 8px;
    margin-left: 120px;
    font-size: 25px;
    line-height: 1.2;
  }
  .rule {
    position: absolute;
    left: 150px;
    top: 240px;
    width: 530px;
    height: 2px;
    background: var(--ink);
  }
  .contact {
    position: absolute;
    left: 380px;
    top: 286px;
  }
  .contact__name {
    font-size: 54px;
    font-weight: 400;
    white-space: nowrap;
  }
  .services {
    list-style: none;
    margin-top: 40px;
    margin-left: 110px;
    font-size: 30px;
    line-height: 1.55;
    white-space: nowrap;
  }
</style>
</head>
<body>
  <article class="card">
    <div class="card__photo" role="img" aria-label="Photo of a handyman with tool belt in front of a suburban house and lawn"></div>

    <header class="brand">
      <h1 class="brand__name">412 SILVER HAWK DETAILING</h1>
      <p class="brand__tagline">residential window cleaning &amp;<br>general handyman maintenance</p>
    </header>

    <div class="rule"></div>

    <section class="contact">
      <h2 class="contact__name">Dale Marsh</h2>
      <ul class="services">
        <li>Window Cleaning</li>
        <li>House Maintenance</li>
      </ul>
    </section>
  </article>
</body>
</html>
```